Blue Harbor Inc - Cutting-Edge Biotech Laboratory - Sleek & Sophisticated

Please design a website that has more of a high-tech and high-end feel, with contents outlined in the uploaded file.

Please have main tabs of the following categories: Home, About, FDA & LAWS, Science, Products, Media, Contact.

Media can include all the videos and photos.

Current website: www.blueharborlabs.com - it needs to be much more high-end, sleek and more organized. Please do NOT follow the outlines in the old website, but follow the uploaded CONTENT file.

Target Market(s)

doctors

Industry/Entity Type

Biotechnology

Coding

Coded - Design and coding required

Number of Pages Required

5+ page

Requirements
Must have
• Logo
Nice to have
• Some lotion on the website

```html
<!DOCTYPE html>
<html lang="en">
<head>
<meta charset="utf-8">
<title>Blue Harbor Inc</title>
<link href="https://fonts.googleapis.com/css2?family=Roboto:ital,wght@0,300;0,400;0,500;0,700;1,400&family=Nothing+You+Could+Do&display=swap" rel="stylesheet">
<style>
:root{
  --blue:#1f6fd0;
  --blue-dark:#0b2a55;
  --navy:#030b1c;
  --ink:#1c2233;
  --text:#6b7488;
  --muted:#9aa2b4;
  --line:#d9dde6;
  --soft:#f5f6fa;
  --white:#ffffff;
  --red:#d0342c;
}
*{box-sizing:border-box;margin:0;padding:0}
html,body{width:1200px;height:3232px;overflow:hidden}
body{font-family:"Roboto",Arial,sans-serif;color:var(--ink);background:var(--white);position:relative}
section,header,footer{position:absolute;left:0;width:1200px}
.abs{position:absolute}
.label{font-size:16px;color:var(--muted);font-weight:300}
.heading{font-size:32px;font-weight:400;color:var(--ink)}
.copy{font-size:13px;line-height:22px;color:var(--text)}

/* hero */
.hero{top:0;height:543px;background:radial-gradient(ellipse at 60% 55%,#1b4f9a 0%,#0c2a5a 35%,#050f26 70%,var(--navy) 100%)}
.brand{left:52px;top:0;width:157px;height:140px;background:var(--blue);color:var(--white);display:flex;align-items:flex-end;justify-content:center;padding-bottom:22px;font-size:20px;font-weight:500;letter-spacing:1px}
.nav{top:26px;left:379px;display:flex;gap:0}
.nav a{position:absolute;color:var(--white);text-decoration:none;font-size:14px;font-weight:500;white-space:nowrap}
.pill{height:32px;border-radius:16px;font-size:13px;font-weight:500;display:flex;align-items:center;justify-content:center;top:19px}
.pill.outline{left:939px;width:92px;border:1.5px solid var(--white);color:var(--white)}
.pill.solid{left:1038px;width:119px;background:var(--white);color:var(--ink)}
.hero-title{width:1200px;text-align:center;font-family:"Nothing You Could Do",cursive;color:var(--white);font-size:40px;letter-spacing:3px}
.hero-sub{width:1200px;top:272px;text-align:center;color:var(--white);font-size:20px;font-weight:500}
.play{left:506px;top:326px;width:188px;height:38px;background:var(--white);border-radius:3px;font-size:14px;color:var(--blue-dark);display:flex;align-items:center;justify-content:center;gap:10px}

/* about */
.about{top:543px;height:416px}
.btn{height:34px;border-radius:17px;font-size:13px;display:flex;align-items:center;justify-content:center}
.btn.primary{background:var(--blue);color:var(--white);font-weight:500}
.btn.ghost{border:1px solid var(--line);color:var(--muted)}
.video{left:705px;top:65px;width:411px;height:306px;background:linear-gradient(135deg,#5c5230,#8a7a45 45%,#b7a46a 70%,#4a3f22);border:3px solid #222}
.video-bar{left:0;bottom:0;width:100%;height:16px;background:rgba(0,0,0,.6)}

/* services */
.services{top:959px;height:683px;background:var(--soft)}
.tabs{left:52px;top:233px;width:295px}
.tab{position:absolute;left:0;width:295px;height:82px;display:flex;align-items:center;gap:16px;padding-left:16px;font-size:13px;color:var(--muted)}
.tab.active{background:var(--white);box-shadow:0 2px 8px rgba(0,0,0,.06)}
.dot{width:44px;height:44px;border-radius:50%;flex:none}
.thumb{top:500px;width:200px;height:106px}

/* testimonials */
.testimonials{top:1642px;height:498px}
.center{width:1200px;text-align:center}
.quote{font-size:12.5px;line-height:19px;color:var(--text);font-style:italic}
.who{font-size:13px;color:var(--ink)}
.avatar{width:82px;height:82px;border-radius:50%;background:linear-gradient(135deg,#d9d4ce,#8a7d72)}
.vline{left:599px;top:245px;height:376px;border-left:1.5px dotted var(--blue)}
.hline{left:52px;top:330px;width:1096px;border-top:1.5px dotted var(--blue)}

/* media */
.media{top:2140px;height:614px;background:var(--soft)}
.card{top:209px;width:254px;height:354px;background:var(--white)}
.card-img{left:0;top:0;width:254px;height:188px}
.card h3{position:absolute;left:20px;top:210px;font-size:17px;font-weight:500;color:var(--ink)}
.card p{position:absolute;left:20px;top:240px;width:214px;font-size:12px;line-height:17px;color:var(--text)}
.meta{left:20px;right:20px;top:322px;font-size:11.5px;color:var(--text);display:flex;justify-content:space-between}

/* contacts */
.contacts{top:2754px;height:317px}
.col-head{top:54px;font-size:17px;font-weight:500;color:var(--ink)}
.col-rule{top:80px;height:2px}
.entry{font-size:12px;line-height:17px;color:var(--text)}
.entry b{color:var(--ink);font-weight:500;display:block;margin-bottom:2px}

/* bottom */
.bottom{top:3071px;height:161px;border-top:3px solid var(--blue)}
.bottom-nav{top:48px;left:52px;display:flex;gap:30px;font-size:14px;font-weight:500;align-items:center}
.bottom-links{top:92px;left:52px;display:flex;gap:22px;font-size:11.5px;color:var(--text)}
.bottom-right{top:92px;right:52px;display:flex;gap:22px;font-size:11.5px;color:var(--text)}
.bottom-brand{right:52px;top:40px;font-size:16px;font-weight:500;color:var(--blue);display:flex;align-items:center;gap:8px}
.bottom-edge{left:0;bottom:0;width:1200px;height:6px;background:var(--blue)}
</style>
</head>
<body>

<header class="hero" role="img" aria-label="Dark blue abstract network of glowing connected points">
  <div class="abs brand">BLUE HARBOR</div>
  <nav class="abs nav">
    <a style="left:0">ABOUT US</a>
    <a style="left:99px">FDA &amp; LAWS</a>
    <a style="left:207px">SCIENCE</a>
    <a style="left:297px">PRODUCTS</a>
    <a style="left:401px">MEDIA</a>
  </nav>
  <div class="abs pill outline">Contact Us</div>
  <div class="abs pill solid">Physician's Login</div>
  <h1 class="abs hero-title" style="top:168px;font-weight:400">Leader in Regenerative Medicine</h1>
  <div class="abs hero-title" style="top:218px">Innovator of the Industry</div>
  <div class="abs hero-sub">Never Compromises on Quality</div>
  <div class="abs play">
    <svg width="12" height="12" viewBox="0 0 12 12"><path d="M2 1l9 5-9 5z" fill="var(--blue)"/></svg>
    Interview Marco Deleon
  </div>
</header>

<section class="about">
  <div class="abs label" style="left:52px;top:31px">About Us</div>
  <h2 class="abs heading" style="left:52px;top:56px">Who we are ?</h2>
  <p class="abs copy" style="left:52px;top:112px;width:530px">Blue Harbor Cell Therapy provides Embryonic Stem Cells and unique protocols to doctors in order to help their patients who face major health conditions as well as individuals who simply wish to stay young and healthy.</p>
  <p class="abs copy" style="left:52px;top:190px;width:530px">Over the past five years of development, we have successfully conducted research into targeted major diseases related to kidney, liver and heart failures, we have aided in helping people who have suffered stroke or brain injury to walk or talk again. We have removed all traces of tumor in multiple cancer patients and we have achieved significant results in fighting aging and its physical markers.</p>
  <div class="abs btn primary" style="left:52px;top:331px;width:133px">Contact Us</div>
  <div class="abs btn ghost" style="left:224px;top:331px;width:134px">Read More</div>
  <div class="abs video" role="img" aria-label="Video of an interview with two people seated in a studio">
    <div class="abs video-bar"></div>
  </div>
</section>

<section class="services">
  <div class="abs label" style="left:52px;top:45px">Services</div>
  <h2 class="abs heading" style="left:52px;top:75px">What we do ?</h2>
  <p class="abs copy" style="left:52px;top:130px;width:380px;font-size:12px;line-height:20px">Sed ut perspiciatis unde omnis iste natus error sit voluptatem Neque porro quisquam est, qui dolorem ipsum quia dolor</p>
  <div class="abs tabs">
    <div class="tab active" style="top:0"><span class="dot" role="img" aria-label="Green cell image" style="background:radial-gradient(#5fbf4a,#0d2a10)"></span>FDA &amp; LAWS</div>
    <div class="tab" style="top:78px"><span class="dot" role="img" aria-label="Purple tissue image" style="background:radial-gradient(#8a6cf0,#1d1570)"></span>Tissue Matrix</div>
    <div class="tab" style="top:151px"><span class="dot" role="img" aria-label="Violet bone image" style="background:radial-gradient(#c48ae0,#3a1a5a)"></span>Orthopedics</div>
    <div class="tab" style="top:225px"><span class="dot" role="img" aria-label="Blue molecule image" style="background:radial-gradient(#7cc6f0,#134e8a)"></span>Glossary</div>
    <div class="tab" style="top:296px"><span class="dot" role="img" aria-label="Blue growth factor image" style="background:radial-gradient(#4f8af0,#0d2480)"></span>Classes of growth factors</div>
  </div>
  <h3 class="abs" style="left:414px;top:258px;font-size:22px;font-weight:400;color:var(--ink)">FDA &amp; LAWS</h3>
  <p class="abs copy" style="left:414px;top:310px;width:734px;font-size:12px;line-height:19px">Sed ut perspiciatis unde omnis iste natus error sit voluptatem accusantium doloremque laudantium, totam rem aperiam, eaque ipsa quae ab illo inventore veritatis et quasi architecto beatae vitae dicta sunt explicabo. Nemo enim ipsam voluptatem quia voluptas sit aspernatur aut odit aut fugit, sed quia consequuntur magni dolores eos qui.</p>
  <p class="abs copy" style="left:414px;top:386px;width:734px;font-size:12px;line-height:19px">Sed ut perspiciatis unde omnis iste natus error sit voluptatem accusantium doloremque laudantium, totam rem aperiam, eaque ipsa quae ab illo inventore veritatis et quasi</p>
  <div class="abs" style="left:414px;top:455px;font-size:13px;color:var(--red)">Details ›</div>
  <div class="abs thumb" style="left:414px;background:linear-gradient(135deg,#e9d6c9,#c9a994 60%,#9fd6e0)" role="img" aria-label="Skin care close-up photo"></div>
  <div class="abs thumb" style="left:653px;background:radial-gradient(ellipse at 40% 60%,#7fd0f5,#1f6fc0 60%,#0d3c7a)" role="img" aria-label="Blue microscopic cells photo"></div>
  <div class="abs thumb" style="left:892px;background:linear-gradient(135deg,#e3b79c,#b77a5a 50%,#6a3b2a)" role="img" aria-label="Grid of body treatment photos"></div>
</section>

<section class="testimonials">
  <div class="abs label center" style="top:30px;font-size:14px">Testimonials</div>
  <h2 class="abs heading center" style="top:60px;font-size:30px">What Our Client Says ?</h2>
  <p class="abs copy center" style="top:126px;left:0;font-size:12px;line-height:20px">What our clients say about our services and how we helped us and make<br>them life better than before</p>
  <div class="abs vline"></div>
  <div class="abs hline"></div>

  <p class="abs quote" style="left:52px;top:222px;width:413px;text-align:right">Duis aute irure dolor in reprehenderit in voluptate velit esse cillum dolore eu fugiat nulla pariatur. Excepteur sint occaecat cupidatat non proident, sunt in culpa qui officia deserunt mollit.</p>
  <div class="abs who" style="left:52px;top:292px;width:413px;text-align:right">Alan Brooks, Operations Manager</div>
  <div class="abs avatar" style="left:487px;top:222px" role="img" aria-label="Client portrait"></div>

  <div class="abs avatar" style="left:629px;top:222px" role="img" aria-label="Client portrait"></div>
  <p class="abs quote" style="left:735px;top:222px;width:413px">Provident, similique sunt in culpa qui officia deserunt mollitia animi, id est laborum et dolorum fuga. Et harum quidem rerum facilis est et expedita distinctio. Nam libero tempore, cum soluta nobis.</p>
  <div class="abs who" style="left:735px;top:292px">Nora Vance, Creative Designer</div>

  <p class="abs quote" style="left:52px;top:360px;width:413px;text-align:right">Duis aute irure dolor in reprehenderit in voluptate velit esse cillum dolore eu fugiat nulla pariatur. Excepteur sint occaecat cupidatat non proident, sunt in culpa qui officia deserunt mollit.</p>
  <div class="abs who" style="left:52px;top:430px;width:413px;text-align:right">Ruth Ellis, Manager</div>
  <div class="abs avatar" style="left:487px;top:360px" role="img" aria-label="Client portrait"></div>

  <div class="abs avatar" style="left:629px;top:360px" role="img" aria-label="Client portrait"></div>
  <p class="abs quote" style="left:735px;top:360px;width:413px">At vero eos et accusamus et iusto odio dignissimos ducimus qui blanditiis praesentium voluptatum deleniti atque corrupti quos dolores et quas molestias excepturi sint occaecati asperiores.</p>
  <div class="abs who" style="left:735px;top:430px">Sam Porter, Developer</div>
</section>

<section class="media">
  <div class="abs label" style="left:52px;top:28px">Media</div>
  <h2 class="abs heading" style="left:52px;top:58px">Latest News &amp; Views</h2>
  <p class="abs copy" style="left:52px;top:122px;width:440px;font-size:12px;line-height:20px">Neque porro quisquam est, qui dolorem ipsum quia dolor sit amet, consectetur, adipisci velit, sed quia non</p>

  <article class="abs card" style="left:52px">
    <div class="abs card-img" role="img" aria-label="Photo of a traveller with a leather bag" style="background:linear-gradient(160deg,#c9c4bd,#6d5a48 55%,#3a2a1e)"></div>
    <h3>Standard Post</h3>
    <p>Enim congue blandit. Lorem ipsum dolor sit amet, consectetur adipiscing elit. Quisque...</p>
    <div class="abs meta"><span>▦ 22 June, 2015</span><span>● 0</span></div>
  </article>
  <article class="abs card" style="left:334px">
    <div class="abs card-img" role="img" aria-label="Photo of a glass coffee maker" style="background:linear-gradient(180deg,#f2f0ec,#d8d3cb 55%,#2d2218)"></div>
    <h3>Video Post</h3>
    <p>Ultrices posuere cubilia curae curabitur sit amet tortor ut massa commodo. Vestibulum...</p>
    <div class="abs meta"><span>▦ 22 June, 2015</span><span>● 0</span></div>
  </article>
  <article class="abs card" style="left:614px">
    <div class="abs card-img" role="img" aria-label="Photo of a cafe interior with brick wall" style="background:linear-gradient(160deg,#8a4a2e,#b58a62 55%,#e2d6c4)"></div>
    <h3>Post with Image</h3>
    <p>Enim congue blandit. Lorem ipsum dolor sit amet, consectetur adipiscing elit. Quisque...</p>
    <div class="abs meta"><span>▦ 22 June, 2015</span><span>● 0</span></div>
  </article>
  <article class="abs card" style="left:896px">
    <div class="abs card-img" role="img" aria-label="Photo of a leather wallet on a table" style="background:linear-gradient(170deg,#c9ccd6,#9a8778 55%,#5a3d2a)"></div>
    <h3>Image Post</h3>
    <p>Ultrices posuere cubilia curae curabitur sit amet tortor ut massa commodo. Vestibulum...</p>
    <div class="abs meta"><span>▦ 22 June, 2015</span><span>● 3</span></div>
  </article>
</section>

<section class="contacts">
  <div class="abs col-head" style="left:52px">Doctors Offices</div>
  <div class="abs col-rule" style="left:52px;width:534px;background:var(--blue)"></div>
  <div class="abs col-head" style="left:614px">Chief</div>
  <div class="abs col-rule" style="left:614px;width:254px;background:var(--line)"></div>
  <div class="abs col-head" style="left:896px">Headquarters</div>
  <div class="abs col-rule" style="left:896px;width:252px;background:var(--line)"></div>

  <div class="abs entry" style="left:52px;top:116px"><b>Dr. Owen R. Hale</b>Hale Center for Heart Health<br>Lindale, CA 90210</div>
  <div class="abs entry" style="left:334px;top:116px"><b>Dr. Lena Marsh</b>1200 Harbor Blvd #B<br>Riverton TX 75000</div>
  <div class="abs entry" style="left:52px;top:204px"><b>Dr. Paul Wexler</b>4100 W Cedar Rd #120<br>Oakridge MI 48000</div>
  <div class="abs entry" style="left:334px;top:204px;width:260px"><b>Dr. Grant E. Moore</b>Cove Vascular Care - 2200 Elm Ln<br>#105, Fairview TX 75000</div>

  <div class="abs entry" style="left:614px;top:116px"><b>Marco Deleon</b>Chief Scientist<br>+1 (555) 010-2291</div>
  <div class="abs entry" style="left:754px;top:116px"><b>Dana Whitfield</b>Stem Cell Manager<br>+1 (555) 010-6044</div>

  <div class="abs entry" style="left:896px;top:116px;width:120px"><b>Texas</b>2100 West Harbor Road<br>Lakeview Hills<br>MI, 48000</div>
  <div class="abs entry" style="left:1036px;top:116px"><b>Email</b>info@blueharborlabs.com</div>
</section>

<footer class="bottom">
  <div class="abs bottom-nav">
    <svg width="14" height="14" viewBox="0 0 14 14"><circle cx="6" cy="6" r="4.5" fill="none" stroke="var(--ink)" stroke-width="1.6"/><path d="M9.5 9.5l3.5 3.5" stroke="var(--ink)" stroke-width="1.6"/></svg>
    <span>Help &amp; Contact</span><span>FDA &amp; LAWS</span><span>Science</span><span>Products</span><span>Physician's Login</span>
  </div>
  <div class="abs bottom-brand"><span style="width:12px;height:12px;border-radius:50%;background:var(--blue)"></span>BLUE HARBOR</div>
  <div class="abs bottom-links"><span>About</span><span>Media</span><span>Careers</span><span>Public Policy</span><span>Sitemap</span><span>People</span><span>Partners</span></div>
  <div class="abs bottom-right"><span>© 2006 - 2018</span><span>Privacy</span><span>Legal</span><span>Feedback</span></div>
  <div class="abs bottom-edge"></div>
</footer>

</body>
</html>
```